Marwick Law Letterhead

We need a new letterhead design for a Law Firm. The address for the law firm is 1475 Calloway Street, Suite 210, Houston, Texas 77041. Phone Number: 832-361-9027; Fax Number: 832-614-7359. The logo is uploaded to the project.

```html
<!DOCTYPE html>
<html lang="en">
<head>
<meta charset="utf-8">
<title>Marwick Law Letterhead</title>
<link href="https://fonts.googleapis.com/css2?family=Montserrat:wght@400;500;600&display=swap" rel="stylesheet">
<style>
  :root {
    --navy: #1c2f5e;
    --red: #d71c27;
    --red-dark: #6c0612;
    --ink: #2b2b2b;
    --paper: #ffffff;
    --backdrop: #e8e8e8;
  }
  * { margin: 0; padding: 0; box-sizing: border-box; }
  html, body {
    width: 1154px; height: 1200px; overflow: hidden;
    background: var(--backdrop);
    font-family: "Montserrat", sans-serif;
  }
  .letterhead {
    position: absolute; left: 148px; top: 0;
    width: 858px; height: 1200px;
    background: var(--paper);
    overflow: hidden;
  }
  .page-art { position: absolute; inset: 0; width: 858px; height: 1200px; }
  .brand {
    position: absolute; left: 33px; top: 70px;
    display: flex; align-items: center; gap: 12px;
  }
  .brand-dot { width: 30px; height: 30px; border-radius: 50%; background: var(--navy); }
  .brand-name { font-size: 31px; font-weight: 600; color: var(--navy); letter-spacing: 0.5px; }
  .contact {
    position: absolute; left: 604px; top: 62px;
    color: #fff; font-size: 14.5px; line-height: 18.5px;
  }
  .contact-lines { list-style: none; margin-top: 9px; }
  .contact-lines li { display: flex; align-items: center; gap: 9px; height: 21px; }
  .contact-lines svg { width: 14px; height: 14px; margin-left: -2px; }
  .letter { position: absolute; left: 33px; top: 284px; width: 795px; color: var(--ink); }
  .recipient { font-size: 14.5px; line-height: 21.3px; color: #1b1b1b; margin-left: -2px; }
  .body-copy p {
    font-size: 14.5px; line-height: 21.3px;
    text-align: justify; margin-bottom: 21px;
  }
  .closing { position: absolute; left: 31px; top: 978px; font-size: 17.5px; color: #1b1b1b; }
  .signature {
    position: absolute; left: 31px; top: 1010px;
    width: 96px; height: 30px; background: #ececec; border-radius: 3px;
  }
</style>
</head>
<body>
  <main class="letterhead">
    <svg class="page-art" viewBox="0 0 858 1200" aria-hidden="true">
      <defs>
        <linearGradient id="header-red" x1="0" y1="0" x2="1" y2="1">
          <stop offset="0.35" stop-color="#d71c27"/>
          <stop offset="1" stop-color="#6c0612"/>
        </linearGradient>
        <linearGradient id="footer-red" x1="0" y1="0" x2="1" y2="0">
          <stop offset="0.4" stop-color="#d71c27"/>
          <stop offset="1" stop-color="#6c0612"/>
        </linearGradient>
      </defs>
      <polygon class="header-stripe" points="400,0 414,0 561,193 549,193" fill="#1c2f5e"/>
      <polygon class="header-band" points="425,0 858,0 858,193 573,193" fill="url(#header-red)"/>
      <path class="footer-band" d="M0 1059 Q429 1245 858 1059 V1200 H0 Z" fill="url(#footer-red)"/>
      <path class="footer-swoosh" d="M39 1067 Q429 1210 808 1072 Q429 1226 39 1067 Z" fill="#1c2f5e"/>
    </svg>

    <header>
      <div class="brand">
        <span class="brand-dot"></span>
        <span class="brand-name">Marwick Law</span>
      </div>
      <address class="contact">
        1475 Calloway Street,<br>Suite 210, Houston,<br>Texas 77041
        <ul class="contact-lines">
          <li>
            <svg viewBox="0 0 24 24" fill="#fff"><path d="M6.6 10.8a15 15 0 0 0 6.6 6.6l2.2-2.2c.3-.3.7-.4 1-.2 1.1.4 2.3.6 3.6.6.6 0 1 .4 1 1V20c0 .6-.4 1-1 1A17 17 0 0 1 3 4c0-.6.4-1 1-1h3.5c.6 0 1 .4 1 1 0 1.3.2 2.5.6 3.6.1.3 0 .7-.2 1z"/></svg>
            <span>832-361-9027</span>
          </li>
          <li>
            <svg viewBox="0 0 24 24" fill="#fff"><path d="M7 3h10v5H7zM4 9h16a2 2 0 0 1 2 2v6h-4v4H6v-4H2v-6a2 2 0 0 1 2-2zm4 7v3h8v-3z"/></svg>
            <span>832-614-7359</span>
          </li>
        </ul>
      </address>
    </header>

    <section class="letter">
      <div class="recipient">
        Mr/s<br>First Name and Last Name<br>Company Name<br>Address
      </div>
      <div class="body-copy">
        <p>Lorem ipsum dolor sit amet,consectetur adipiscing sed do eiusmod tempor incididunt laboreet dolore magna aliqua.Ut enim ad minim.veniam, quis nostrud exercitation ullamco laboris nisi ut aliquip exea commodo consequat.Lorem ipsum dolor sit amet,consectetur adipiscing sed do eiusmod tempor incididunt.labore et dolore magna aliqua. Ut enim</p>
        <p>Lorem ipsum dolor sit amet, consectetur adipiscing sed do eiusmod tempor incididunt labore et dolore magna aliqua. Ut enim ad minim veniam, quis nostrud exercitation ullamco laboris nisi ut aliquip exea commodo consequat.Duis aute irure dolor in reprehenderit in voluptate velit esse cillum irure dolor in reprehenderit in voluptate velit esse irure</p>
        <p>Lorem ipsum dolor sit amet, consectetur adipiscing sed do eiusmod tempor incididunt labore et dolore magna aliqua. consequat. Duis aute irure dolor in.reprehenderit in voluptate velit esse cillum dolore eu fugiat nulla pariatur. Excepteur sint occaecat cupidatat non proident, sunt in culpa qui officia deserunt mollit,</p>
        <p>Lorem ipsum dolor sit amet, consectetur adipiscing sed do eiusmod tempor incididunt labore et dolore magna aliqua. Ut enim Lorem ipsum dolor sit amet, consectetur adipiscing sed do eiusmod tempor incididunt labore et dolore magna aliqua. Ut enim Lorem ipsum aliqua.ipsum</p>
        <p>Lorem ipsum dolor sit amet, consectetur adipiscing sed do eiusmod tempor incididunt labore et dolore magna aliqua. Ut enim ad minim veniam, quis nostrud exercitation ullamco laboris nisi ut aliquip exea commodo consequat.Duis aute irure dolor in reprehenderit in voluptate velit esse cillum irure dolor in reprehenderit in voluptate velit esse irure</p>
        <p>Lorem ipsum dolor sit amet, consectetur adipiscing sed do eiusmod tempor incididunt labore et dolore magna aliqua. Ut enim ad minim veniam, quis nostrud exercitation ullamco laboris nisi ut aliquip exea commodo consequat.Duis aute irure dolor in reprehenderit in voluptate velit esse cillum irure dolor in reprehenderit in voluptate velit esse irure</p>
      </div>
    </section>

    <p class="closing">Regards</p>
    <div class="signature" role="img" aria-label="Handwritten signature of the sender"></div>
  </main>
</body>
</html>
```